Help Give House Painter “Fresh” Website Makeover!

A residential and commercial painting company based in Albuquerque, NM, USA needs a fresh, new, fun, and playful--yet, simple, elegant and professional--website made.

Here is a link to their existing site:

http://corvelcoatings.example/

We want to keep a similar site structure., So the navigation layout will stay the same. However, the video is too small, is too far over in the sidebar, and the overall design is amateur at best. We want something bright, colorful and bold!

We will need a space for the Video above the fold, and there needs to be space in the design for Testimonials, Specials and Images. It’s also very important to have the Pellham Roster awards that you see on his current website.

Please also include somewhere in the Design icons for YouTube, Facebook, Google+ and LinkedIn.

Here are some examples to look at to get your creative juices flowing!

http://brightloombrush.example/

http://www.tkvr.example/

http://www.marblow-tennick.example/

http://www.quarrypages.example/painting-company-niche-website/

http://www.brisklayoutdepot.example/website-templates/painting-company-website-template-53817.html

We have accounts at both lumavault.example and pixaroo.example. If you use placeholder images from there, that's fine. We can buy the images when and if your design is selected.

Target Market(s)

The audience is the average middle class homeowner to higher upper class. This should appeal to families, couples, and singles who own a home.

Industry/Entity Type

Residential

Font styles to use
Sans Serif

Requirements
Must have
• - - Lots of color! It's a site about painting homes. People like a variety of colors. Bring out your inner artist, and get bold with your colors!

- - A video place holder. As you can see, there is a video on the existing site, but it's small and hidden. Make it big and put it top left, or in the center.

- -Detailed and organized PSD structure. We're going to turn your design into a website, and to make that work soothly, we ask that you organize you PSD well: name your layers, keep things separated, group and ungroup as necessary, etc.

- A sidebar that goes down the right side of an interior page. We need a homepage, and also one [1] interior page template. We don't need you to make a design for each page. Just the homepage, followed by a simple interior page design that requires only the header/navigation, and a sidebar down the right side.
Should not have
• - Coding. This is a design project only.

```html
<!DOCTYPE html>
<html lang="en">
<head>
<meta charset="utf-8">
<title>Corvel Coatings – Home</title>
<link rel="stylesheet" href="https://fonts.googleapis.com/css2?family=Oswald:wght@400;500&family=Open+Sans:wght@400;600;700;800&family=Arimo:wght@400;700&display=swap">
<style>
:root{
  --blue:#1a56b0;
  --navy:#0f2160;
  --red:#e8202a;
  --orange:#f8b533;
  --orange-dark:#f19d1a;
  --sky:#1c8fdc;
  --ink:#222;
  --text:#444;
  --muted:#8a8a8a;
  --line:#e2e2e2;
  --card:#efefef;
  --footer:#0d0d0d;
  --footer-panel:#3a3a3a;
}
*{box-sizing:border-box;margin:0;padding:0}
html,body{width:883px;height:1200px;overflow:hidden;background:#fff}
body{position:relative;font-family:"Open Sans",Arial,sans-serif;color:var(--text)}
.abs{position:absolute}

/* header */
.site-header{position:absolute;left:0;top:0;width:883px;height:108px;background:#fff;border-top:3px dotted var(--red)}
.brand-dot{left:98px;top:16px;width:72px;height:72px;border-radius:50%;background:var(--blue)}
.brand-name{left:184px;top:20px;font:800 28px/1 "Open Sans",sans-serif;color:var(--blue);letter-spacing:-.5px}
.brand-tagline{left:186px;top:62px;font:700 13px/1 "Open Sans",sans-serif;color:var(--ink)}
.award{width:50px;height:66px;top:14px}
.award-label{top:85px;font:700 12px/1 "Open Sans",sans-serif;color:var(--ink);white-space:nowrap}
.contact-line{right:100px;font:600 12px/1 "Open Sans",sans-serif;color:var(--sky);display:flex;align-items:center;gap:6px}
.social{top:66px;width:28px;height:28px;border-radius:50%;border:2px dashed #c9a040;background:var(--orange)}
.social.alt{background:#6d6d6d}
.social.red{background:#c92a2a}

/* navigation */
.main-nav{position:absolute;left:0;top:108px;width:883px;height:41px;background:linear-gradient(#fcc24b,var(--orange-dark));display:flex}
.main-nav a{position:absolute;top:0;height:41px;line-height:41px;font:700 10.5px/41px Arimo,Arial,sans-serif;color:#1b1b1b;text-decoration:none;white-space:nowrap}
.main-nav a.current{background:var(--blue);color:#fff;width:55px;text-align:center}

/* hero */
.hero{position:absolute;left:0;top:149px;width:883px;height:324px;background:linear-gradient(90deg,#f2ede6 0%,#efe9e1 55%,#e9e3da 100%)}
.hero-wall{left:485px;top:0;width:398px;height:324px;background:linear-gradient(90deg,#3a6e8e 0%,#3a6e8e 25%,#efe9e1 25%,#efe9e1 28%,#9c2fa5 28%,#9c2fa5 51%,#eee7dd 51%,#eee7dd 100%)}
.hero-ladder{left:744px;top:22px;width:98px;height:302px;background:linear-gradient(90deg,#5ba43a,#3f8a27)}
.video{left:96px;top:187px;width:345px;height:274px;border-radius:6px;overflow:hidden;background:#222}
.video-frame{width:345px;height:250px;background:linear-gradient(135deg,#9ccc5c 0%,#cfd8c8 45%,#6b8fb8 100%)}
.video-bar{position:absolute;left:0;bottom:0;width:100%;height:24px;background:#151515;color:#fff;font:600 8px/24px "Open Sans",sans-serif}
.estimate{left:522px;top:200px;width:244px;height:273px;background:rgba(34,34,34,.9)}
.estimate-title{height:34px;background:var(--red);color:#fff;font:500 16px/34px Oswald,sans-serif;padding-left:18px;letter-spacing:.3px}
.field{position:absolute;left:18px;width:206px;height:20px;background:#fff;border-radius:3px;font:600 9px/20px "Open Sans",sans-serif;color:#666;padding-left:7px}
.field.tall{height:45px}
.captcha-label{position:absolute;left:18px;top:193px;font:700 10px/1 "Open Sans",sans-serif;color:#fff}
.captcha{position:absolute;left:158px;top:191px;width:64px;height:18px;background:var(--red);color:#fff;font:700 italic 9px/18px Arial,sans-serif;letter-spacing:5px;text-align:center}
.btn{position:absolute;background:var(--sky);color:#fff;font:700 10px/1 "Open Sans",sans-serif;display:flex;align-items:center;justify-content:center;border-radius:2px}

/* welcome */
.welcome-title{left:96px;top:494px;font:400 17px/1 Oswald,sans-serif;color:var(--ink)}
.welcome-title span{color:var(--red)}
.rule{left:96px;top:520px;width:686px;height:1px;background:var(--line)}
.rule-accent{left:96px;top:519px;width:51px;height:3px;background:var(--red)}
.copy{left:96px;width:700px;font:400 10.2px/17px "Open Sans",sans-serif;color:#3d3d3d;white-space:nowrap;letter-spacing:-.05px}

/* feature cards */
.card{top:700px;width:212px;height:255px;background:var(--card);border-radius:6px 6px 4px 4px;box-shadow:0 3px 4px rgba(0,0,0,.15);overflow:hidden}
.card-head{height:55px;padding:6px 0 0 15px;font:400 16px/22px Oswald,sans-serif;color:#fff;text-transform:uppercase}
.card-photo{position:absolute;left:12px;top:67px;width:190px;height:82px;border:3px solid}
.card-text{position:absolute;left:12px;top:158px;width:190px;font:400 10.3px/13.5px "Open Sans",sans-serif;color:#222}
.card-more{position:absolute;left:12px;top:231px;font:700 8.5px/1 Arimo,Arial,sans-serif;color:#222}

/* footer */
.site-footer{position:absolute;left:0;top:992px;width:883px;height:208px;background:var(--footer)}
.testimonials{left:96px;top:0;width:212px;height:208px;background:var(--footer-panel)}
.testimonials-title{position:absolute;left:46px;top:16px;font:400 17px/1 Oswald,sans-serif;color:#fff}
.quote{position:absolute;left:8px;top:50px;width:194px;height:107px;background:#fff;border-radius:5px;padding:8px 8px 0 26px;font:italic 400 9.2px/15.2px Arimo,Arial,sans-serif;color:#222}
.quote-mark{position:absolute;left:8px;top:2px;font:700 30px/1 Georgia,serif;color:#ccc}
.client-avatar{position:absolute;left:140px;top:140px;width:54px;height:54px;border-radius:50%;border:3px solid #ddd;background:linear-gradient(#d9c3b5,#8d8d8d)}
.client-name{position:absolute;left:22px;top:182px;font:700 10.5px/1 Arimo,Arial,sans-serif;color:#fff}
.ft{color:#fff;font:400 11px/1 "Open Sans",sans-serif}
.ft-head{font:400 13px/1 Oswald,sans-serif;color:#fff}
.seal{height:52px;top:98px;border-radius:3px}
.copyright{right:100px;top:182px;font-weight:700;font-size:9.5px;letter-spacing:.2px;white-space:nowrap}
</style>
</head>
<body>

<header class="site-header">
  <div class="abs brand-dot"></div>
  <div class="abs brand-name">Corvel Coatings</div>
  <div class="abs brand-tagline">Not Just Another Painter</div>

  <svg class="abs award" style="left:411px" viewBox="0 0 50 66" role="img" aria-label="Pellham Roster award badge">
    <path d="M3 2h44v34c0 14-10 23-22 28C13 59 3 50 3 36z" fill="#d9a928" stroke="#8b6a15" stroke-width="2"/>
  </svg>
  <div class="abs award-label" style="left:385px">Exterior Painting</div>
  <svg class="abs award" style="left:525px" viewBox="0 0 50 66" role="img" aria-label="Pellham Roster award badge">
    <path d="M3 2h44v34c0 14-10 23-22 28C13 59 3 50 3 36z" fill="#d9a928" stroke="#8b6a15" stroke-width="2"/>
  </svg>
  <div class="abs award-label" style="left:500px">Interior Painting</div>

  <div class="abs contact-line" style="top:13px;font-size:13px">
    <svg width="10" height="13" viewBox="0 0 10 13"><path d="M2 0h3l1 3-2 1c1 2 2 4 4 5l1-2 3 1-1 3c-5 0-10-5-9-11z" fill="currentColor"/></svg>
    505-555-0143
  </div>
  <div class="abs contact-line" style="top:39px;font-size:11px">
    <svg width="15" height="10" viewBox="0 0 15 10"><rect width="15" height="10" fill="currentColor"/><path d="M0 0l7.5 6L15 0" stroke="#fff" fill="none"/></svg>
    info@corvelcoatings.example
  </div>
  <div class="abs social" style="left:656px" aria-label="Social link"></div>
  <div class="abs social alt" style="left:690px" aria-label="Social link"></div>
  <div class="abs social red" style="left:724px" aria-label="Social link"></div>
  <div class="abs social" style="left:758px;background:#4da7d8" aria-label="Social link"></div>
</header>

<nav class="main-nav">
  <a class="current" style="left:96px" href="#">HOME</a>
  <a style="left:168px" href="#">About Us</a>
  <a style="left:232px" href="#">Residential Painting</a>
  <a style="left:347px" href="#">Commercial Painting</a>
  <a style="left:471px" href="#">Specials</a>
  <a style="left:538px" href="#">Blog</a>
  <a style="left:580px" href="#">Testimonials</a>
  <a style="left:658px" href="#">Contact Us</a>
</nav>

<section class="hero">
  <div class="abs hero-wall" role="img" aria-label="Wall with colourful paint swatches"></div>
  <div class="abs hero-ladder" role="img" aria-label="Green ladder leaning on the wall" style="top:22px;opacity:.85"></div>
</section>

<div class="abs video">
  <div class="video-frame" role="img" aria-label="Video still: couple holding paint rollers in a freshly painted room"></div>
  <svg class="abs" style="left:159px;top:110px" width="28" height="28" viewBox="0 0 28 28"><circle cx="14" cy="14" r="13" fill="#fff"/><path d="M11 8l9 6-9 6z" fill="#222"/></svg>
  <div class="video-bar">
    <svg class="abs" style="left:9px;top:7px" width="9" height="10" viewBox="0 0 9 10"><path d="M0 0l9 5-9 5z" fill="#fff"/></svg>
    <span class="abs" style="left:30px">04:59</span>
    <span class="abs" style="left:58px;top:10px;width:186px;height:4px;background:#444"></span>
    <span class="abs" style="left:58px;top:10px;width:62px;height:4px;background:#777"></span>
    <span class="abs" style="left:264px">10:35</span>
    <svg class="abs" style="left:302px;top:6px" width="12" height="12" viewBox="0 0 12 12"><path d="M0 4h3l4-3v10L3 8H0z M9 3c2 2 2 4 0 6" fill="#fff" stroke="#fff"/></svg>
    <svg class="abs" style="left:320px;top:6px" width="12" height="12" viewBox="0 0 12 12"><path d="M1 1l10 10M1 1h4M1 1v4M11 11H7M11 11V7" stroke="#fff" stroke-width="1.6"/></svg>
  </div>
</div>

<form class="abs estimate">
  <div class="estimate-title">SCHEDULE FREE ESTIMATE</div>
  <div class="field" style="top:45px">Your Name</div>
  <div class="field" style="top:77px">Phone Number</div>
  <div class="field" style="top:107px">Email</div>
  <div class="field tall" style="top:136px;line-height:20px">Describe What Needs To Be Done</div>
  <div class="captcha-label">Please type the Following:</div>
  <div class="captcha">EBTL</div>
  <div class="field" style="top:216px"></div>
  <div class="btn" style="left:18px;top:243px;width:70px;height:24px">Continue</div>
</form>

<h1 class="abs welcome-title">Welcome To <span>Corvel Coatings</span></h1>
<div class="abs rule"></div>
<div class="abs rule-accent"></div>
<p class="abs copy" style="top:535px">Lorem ipsum dolor sit amet, consectetuer adipiscing elit, sed diam nonummy nibh euism od tincidunt ut laoreet dolore magna aliquam erat<br>volutpat. Ut wisi enim ad minim venia m, quis nostrud exerci in amet ullamcorper suscipit lobortis nisl ut aliquip ex ea comsed diam nonummy<br>nibh euism od tincidunt uopre laoreet dolore magna aliquam erat volutpat.</p>
<p class="abs copy" style="top:594px">Lorem ipsum dolor sit amet, consectetuer adipiscing elit, sed diam nonummy nibh euism od tincidunt ut in laoreet dolore magna aliquam erat volutpat.<br>Ut wisi enim ad minim venia m, quis nostrud exerci tationperq ullamcorper suscipit lobortis nisl ut..<br>in laoreet dolore magna aliquam erat volutpat. Ut wisi enim ad minim venia m, quis nostrud exerci tationperq ullamcorper suscipit lobortis nisl ut..</p>
<div class="btn" style="left:96px;top:655px;width:70px;height:24px">Read More</div>

<article class="abs card" style="left:96px">
  <div class="card-head" style="background:var(--navy)">Our Painting<br>in Albuquerque</div>
  <div class="card-photo" role="img" aria-label="Couple painting a wall green" style="border-color:var(--navy);background:linear-gradient(90deg,#8fc453,#c9d6c2 60%,#5b7aa6)"></div>
  <p class="card-text">Lorem ipsum dolor sit ametuer adipiscingi elit, sed diam nmy nibh euismod tincidunt ut laoreet dolore magna am erat visi enim ad minim veniam, quis nostrud exerci</p>
  <div class="card-more">READ MORE »</div>
</article>
<article class="abs card" style="left:334px">
  <div class="card-head" style="background:var(--red)">Albuquerque<br>Painter Videos</div>
  <div class="card-photo" role="img" aria-label="Painter with roller beside a ladder" style="border-color:var(--red);background:linear-gradient(90deg,#a9d4ee,#dfeef7 50%,#6fb6e0)"></div>
  <p class="card-text">Lorem ipsum dolor sit ametuer adipiscingi elit, sed diam nmy nibh euismod tincidunt ut laoreet dolore magna am erat visi enim ad minim veniam, quis nostrud exerci</p>
  <div class="card-more">READ MORE »</div>
</article>
<article class="abs card" style="left:573px">
  <div class="card-head" style="background:var(--orange)">Happy Albuquerque<br>Painting Customers</div>
  <div class="card-photo" role="img" aria-label="Smiling customers holding paint rollers" style="border-color:var(--orange);background:linear-gradient(90deg,#9ccc5c,#e0d2c2 50%,#7aa0c8)"></div>
  <p class="card-text">Lorem ipsum dolor sit ametuer adipiscingi elit, sed diam nmy nibh euismod tincidunt ut laoreet dolore magna am erat visi enim ad minim veniam, quis nostrud exerci</p>
  <div class="card-more">READ MORE »</div>
</article>

<footer class="site-footer">
  <div class="abs testimonials">
    <svg class="abs" style="left:10px;top:13px" width="26" height="22" viewBox="0 0 26 22"><rect x="1" y="3" width="18" height="18" rx="2" fill="none" stroke="#fff" stroke-width="2"/><path d="M9 14l2-5 12-9 3 3-12 9z" fill="#fff"/></svg>
    <div class="testimonials-title">Client&nbsp;&nbsp;Testimonials</div>
    <div class="quote">
      <span class="quote-mark">“</span>
      Lorem ipsum dolor sit amet consctueropf adipiscing elit, sed diam nonummy nibh euismodg tincidunt ut laoreet dolore magna aliquam eratg volutpat. ut wisi enim ad minim veniam, quis nostrud exerci tation
    </div>
    <svg class="abs" style="left:36px;top:156px" width="16" height="12" viewBox="0 0 16 12"><path d="M0 0h16L2 12z" fill="#fff"/></svg>
    <div class="client-avatar" role="img" aria-label="Client portrait"></div>
    <div class="client-name">Mrs.&nbsp; dapibus eget,</div>
  </div>

  <div class="abs ft-head" style="left:335px;top:17px">Sign up for Newsletter</div>
  <div class="abs" style="left:333px;top:41px;width:210px;height:27px;background:#fff;font:400 9px/27px 'Open Sans',sans-serif;color:#777;padding-left:9px">Enter Your Email</div>
  <div class="abs" style="left:549px;top:41px;width:62px;height:27px;background:var(--navy);color:#fff;font:400 12px/27px Arimo,Arial,sans-serif;text-align:center">SUBMIT</div>
  <div class="abs" style="left:633px;top:24px;width:1px;height:50px;background:#333"></div>
  <div class="abs ft-head" style="left:666px;top:17px">Follow Us On</div>
  <div class="abs social" style="left:661px;top:42px;width:26px;height:26px"></div>
  <div class="abs social alt" style="left:694px;top:42px;width:26px;height:26px"></div>
  <div class="abs social red" style="left:727px;top:42px;width:26px;height:26px"></div>
  <div class="abs social" style="left:758px;top:42px;width:26px;height:26px;background:#4da7d8"></div>
  <div class="abs" style="left:333px;top:86px;width:450px;height:1px;background:#2a2a2a"></div>

  <svg class="abs" style="left:335px;top:106px" width="10" height="14" viewBox="0 0 10 14"><path d="M5 0a5 5 0 0 1 5 5c0 4-5 9-5 9S0 9 0 5a5 5 0 0 1 5-5z" fill="#fff"/><circle cx="5" cy="5" r="2" fill="#000"/></svg>
  <p class="abs ft" style="left:355px;top:105px;width:110px;font-size:9.5px;line-height:16px">Lorem ipsum dolor sit amet, consectetuer adipiscing elit,</p>
  <svg class="abs" style="left:532px;top:106px" width="9" height="13" viewBox="0 0 9 13"><rect x="1" y="0.5" width="7" height="12" rx="1" fill="none" stroke="#fff"/><rect x="2.5" y="2" width="4" height="7" fill="#fff"/></svg>
  <div class="abs ft" style="left:551px;top:106px">516-555-0172</div>
  <svg class="abs" style="left:480px;top:132px" width="13" height="10" viewBox="0 0 13 10"><path d="M0 4l6.5-4L13 4v6H0z" fill="#fff"/><path d="M0 4l6.5 4L13 4" stroke="#000" fill="none"/></svg>
  <div class="abs ft" style="left:500px;top:132px;font-size:10px">info@corvelcoatings.example</div>

  <div class="abs seal" style="left:646px;width:74px;background:#fff" role="img" aria-label="Business accreditation seal"></div>
  <div class="abs seal" style="left:721px;width:62px;background:#1b2a6b;border:1px solid #fff" role="img" aria-label="Chamber of commerce membership seal"></div>

  <div class="abs" style="left:333px;top:164px;width:450px;height:1px;background:#2a2a2a"></div>
  <div class="abs ft copyright">© 2014 CORVEL COATINGS&nbsp;&nbsp;|&nbsp;&nbsp;All Rights Reserved</div>
</footer>

</body>
</html>
```